Exclusive Offer Verbalia December 2022

A design that includes the company logo company and the text set out below. It could be a season design (winter design). it is a short promo to be sent by email. It should express that the promotion is on translation services.

Title: ESPECIAL DICIEMBRE

Information:

10% Descuento del 13 al 16 de diciembre
8% Después del 13 y hasta el 24 de diciembre

En contenidos web, materiales publicitarios, catàlogos, textos legales, manuales y más.

+30 años de experiencia, ISO 17100, traductores nativos

Target Market(s)

B2B Spain - any company that needs translation services

Industry/Entity Type

Services and Translation

Requirements
Must have
• Please take into account our corporate style guide attached
Nice to have
• A design that suggests a special offer from a serious, professional, technological and solid translation company.
Should not have
• Typical Christmas stationery, colours that don't fit into our company design trend.

```html
<!DOCTYPE html>
<html lang="es">
<head>
<meta charset="utf-8">
<title>Especial Diciembre – Verbalia</title>
<link href="https://fonts.googleapis.com/css2?family=Bebas+Neue&family=Montserrat:wght@500;600;700&family=Russo+One&display=swap" rel="stylesheet">
<style>
  :root {
    --page-bg: #1b4a5e;
    --frost-light: #cfe8f8;
    --frost-mid: #9ccbef;
    --frost-deep: #7fb4e2;
    --title-ink: #25256a;
    --label-ink: #0d2a4d;
    --divider: #2e3a8c;
    --band-left: #262262;
    --band-right: #224a7c;
    --white: #ffffff;
    --brand-blue: #1f4a7e;
    --accent: #e0890f;
    --contact-ink: #1f3a6b;
  }
  * { box-sizing: border-box; margin: 0; padding: 0; }
  html, body { width: 1200px; height: 1200px; overflow: hidden; }
  body { background: var(--page-bg); position: relative; }

  .promo {
    position: absolute; left: 70px; top: 28px;
    width: 1060px; height: 1144px;
    background: var(--white);
    overflow: hidden;
  }

  .frost {
    position: absolute; left: 0; top: 0; width: 1060px; height: 774px;
    background:
      radial-gradient(ellipse at 50% 55%, #b6dcf6 0%, var(--frost-mid) 45%, var(--frost-deep) 70%, var(--frost-light) 100%);
  }

  .promo-title {
    position: absolute; left: 0; right: 0; top: 62px;
    text-align: center;
    font-family: "Bebas Neue", sans-serif;
    font-size: 126px; line-height: 1; letter-spacing: 1px; word-spacing: 24px;
    color: var(--title-ink);
    transform: scaleX(0.83); transform-origin: 50% 50%;
  }

  .offer {
    position: absolute; top: 270px; width: 460px;
    text-align: center;
  }
  .offer--now { left: 27px; }
  .offer--later { left: 555px; }

  .offer-rate {
    height: 160px;
    font-family: "Russo One", sans-serif;
    color: var(--white);
    text-shadow: 0 4px 6px rgba(20, 50, 90, .35);
    line-height: 1;
  }
  .offer-rate .num { font-size: 170px; letter-spacing: -6px; }
  .offer-rate .pct { font-size: 72px; font-style: italic; margin-left: 4px; }

  .offer-label {
    margin-top: 18px;
    font-family: "Bebas Neue", sans-serif;
    font-size: 90px; line-height: 1; letter-spacing: 1px;
    color: var(--label-ink);
  }
  .offer-dates {
    margin-top: 20px;
    font-family: "Montserrat", sans-serif; font-weight: 700;
    font-size: 33px; line-height: 36px;
    color: var(--white);
    text-shadow: 0 2px 4px rgba(20, 50, 90, .45);
  }

  .offer-divider {
    position: absolute; left: 528px; top: 330px;
    width: 3px; height: 244px; background: var(--divider);
  }

  .info-band { position: absolute; top: 774px; left: 0; width: 1060px; height: 174px; display: flex; }
  .info-band p {
    font-family: "Montserrat", sans-serif; font-weight: 500;
    font-size: 24px; line-height: 35px; color: var(--white);
    padding-top: 26px;
  }
  .info-services { width: 530px; background: var(--band-left); text-align: right; padding-right: 16px; padding-left: 30px; }
  .info-credentials { width: 530px; background: var(--band-right); padding-left: 39px; padding-right: 30px; }

  .footer { position: absolute; top: 948px; left: 0; width: 1060px; height: 196px; }

  .brand { position: absolute; left: 86px; top: 44px; display: flex; align-items: center; gap: 24px; }
  .brand-mark { width: 100px; height: 100px; background: var(--brand-blue); }
  .brand-name {
    font-family: "Montserrat", sans-serif; font-weight: 700;
    font-size: 40px; line-height: 1; color: var(--brand-blue); letter-spacing: 1px;
  }
  .brand-tagline {
    margin-top: 12px;
    font-family: "Montserrat", sans-serif; font-weight: 700;
    font-size: 14px; line-height: 19px; color: var(--brand-blue);
  }

  .footer-divider { position: absolute; left: 528px; top: 20px; width: 3px; height: 150px; background: var(--divider); }

  .contact { position: absolute; left: 586px; top: 40px; font-family: "Montserrat", sans-serif; font-weight: 500; font-size: 18px; color: var(--contact-ink); }
  .contact-row { display: flex; align-items: center; gap: 34px; height: 36px; }
  .contact-item { display: flex; align-items: center; gap: 12px; }
  .contact-item svg { width: 18px; height: 18px; fill: var(--accent); }
  .social { display: flex; gap: 8px; margin-top: 14px; }
  .social span { width: 35px; height: 35px; border-radius: 50%; background: var(--accent); }
</style>
</head>
<body>
  <main class="promo">
    <section class="frost" role="img" aria-label="Fondo de escarcha invernal azul con copos de nieve"></section>

    <h1 class="promo-title">ESPECIAL DICIEMBRE</h1>

    <div class="offer offer--now">
      <div class="offer-rate"><span class="num">10</span><span class="pct">%</span></div>
      <div class="offer-label">DESCUENTO</div>
      <div class="offer-dates">del 13 al 16 de<br>diciembre</div>
    </div>

    <div class="offer-divider"></div>

    <div class="offer offer--later">
      <div class="offer-rate"><span class="num">8</span><span class="pct">%</span></div>
      <div class="offer-label">DESPUÉS</div>
      <div class="offer-dates">del 13 y hasta el 24<br>de diciembre</div>
    </div>

    <section class="info-band">
      <div class="info-services"><p>En contenidos web, materiales publicitarios, catàlogos, textos legales, manuales y más.</p></div>
      <div class="info-credentials"><p>+30 años de experiencia, ISO 17100, traductores nativos</p></div>
    </section>

    <footer class="footer">
      <div class="brand">
        <div class="brand-mark"></div>
        <div>
          <div class="brand-name">VERBALIA</div>
          <div class="brand-tagline">SERVICIOS LINGÜÍSTICOS<br>PROFESIONALES</div>
        </div>
      </div>

      <div class="footer-divider"></div>

      <div class="contact">
        <div class="contact-row">
          <span class="contact-item">
            <svg viewBox="0 0 24 24" aria-hidden="true"><path d="M6.6 10.8a15 15 0 0 0 6.6 6.6l2.2-2.2a1 1 0 0 1 1-.25 11.4 11.4 0 0 0 3.6.57 1 1 0 0 1 1 1V20a1 1 0 0 1-1 1A17 17 0 0 1 3 4a1 1 0 0 1 1-1h3.5a1 1 0 0 1 1 1c0 1.25.2 2.45.57 3.57a1 1 0 0 1-.25 1z"/></svg>
            +34 600 000 000
          </span>
          <span class="contact-item">
            <svg viewBox="0 0 24 24" aria-hidden="true"><path d="M2 5h20v14H2z" opacity=".9"/><path d="M2 5l10 8 10-8" fill="none" stroke="#fff" stroke-width="2"/></svg>
            info@verbalia.example
          </span>
        </div>
        <div class="contact-row">
          <span class="contact-item">
            <svg viewBox="0 0 24 24" aria-hidden="true"><path d="M12 2a7 7 0 0 0-7 7c0 5.2 7 13 7 13s7-7.8 7-13a7 7 0 0 0-7-7zm0 9.5A2.5 2.5 0 1 1 12 6.5a2.5 2.5 0 0 1 0 5z"/></svg>
            C/ Ejemplo 00, 0 º - 0 ª, 00000 Ciudad
          </span>
        </div>
        <div class="social" aria-label="Redes sociales">
          <span></span><span></span><span></span><span></span>
        </div>
      </div>
    </footer>
  </main>
</body>
</html>
```